Commercial Swimming Pool - Design-Build Contractor Website Design

I need a new website that will feature our newly developed logo and trade name as well as provide a fully updated site experience. We are not a residential builder - we strictly design and install high-end commercial pools. I need the website to highlight our portfolio and communicate the various types of projects in which we specialize. I want the effect of the site to reflect the high-end nature of our services - projects like the 57th floor spa at the Phila Silver Willow, the aquatic therapy portion of the Phila Ravenhawks training facility, a 5om indoor competition pool for the prestigious Dallowmere Academy, the indoor water park at The Quenwick Lodge or the recent country club renovation projects we've completed in our region (to name a few examples).
Need extra days to review

```html
<!DOCTYPE html>
<html lang="en">
<head>
<meta charset="utf-8">
<title>Calloway Aquatics — Commercial Pools</title>
<link href="https://fonts.googleapis.com/css2?family=Poppins:wght@400;500;600;700&display=swap" rel="stylesheet">
<style>
:root{
  --navy:#0d1f5c;
  --navy-deep:#0a1848;
  --sky:#3ab4e6;
  --frame:#3aa8e0;
  --pale:#d4edf7;
  --white:#ffffff;
  --ghost:rgba(120,145,190,.22);
  --text:#1b2540;
}
*{margin:0;padding:0;box-sizing:border-box}
html,body{width:1200px;height:5268px;overflow:hidden}
body{font-family:"Poppins",sans-serif;color:var(--text);background:var(--white)}
.page{position:relative;width:1200px;height:5268px;overflow:hidden}
.abs{position:absolute}
.photo{position:absolute;border-radius:50%;border:8px solid var(--white);box-shadow:0 0 0 2px rgba(13,31,92,.25)}
.pill{position:absolute;display:flex;align-items:center;justify-content:center;border-radius:30px;font-weight:600;text-transform:uppercase}
.pill--navy{background:var(--navy);color:var(--white);font-size:12px}
.pill--sky{background:var(--sky);color:var(--white)}
.ghost-word{position:absolute;writing-mode:vertical-rl;transform:rotate(180deg);font-weight:700;font-size:120px;color:var(--ghost);line-height:1;letter-spacing:2px}
.section-title{position:absolute;left:0;width:1200px;text-align:center;color:var(--navy);font-weight:700;font-size:50px;letter-spacing:-.5px}

/* top bar */
.topbar{top:0;left:0;width:1200px;height:45px;background:var(--navy)}
.social{position:absolute;top:9px;width:27px;height:27px;border:2px solid var(--white);border-radius:50%}
.topbar__item{position:absolute;top:0;height:45px;display:flex;align-items:center;gap:10px;color:var(--white);font-size:11px}
.topbar__icon{width:26px;height:26px;border:2px solid var(--white);border-radius:50%;display:flex;align-items:center;justify-content:center}

/* header */
.header{top:45px;left:0;width:1200px;height:105px;background:var(--white)}
.brand{position:absolute;display:flex;align-items:center;gap:12px;color:var(--navy);font-weight:700;font-size:26px;line-height:28px;letter-spacing:1px}
.brand__name{display:flex;flex-direction:column;white-space:nowrap}
.brand__dot{width:44px;height:44px;border-radius:50%;background:var(--sky);flex:none}
.nav a{position:absolute;top:40px;font-size:13px;color:var(--navy);text-decoration:none;font-weight:500;white-space:nowrap}

/* hero */
.hero{top:150px;left:0;width:1200px;height:549px;background:linear-gradient(180deg,#3d5a6e 0%,#2f6e9a 35%,#1f5aa8 65%,#12357e 100%)}
.hero__title{position:absolute;top:148px;width:1200px;text-align:center;color:var(--white);font-weight:700;font-size:58px;line-height:66px;letter-spacing:-1px}
.hero__sub{position:absolute;top:315px;width:1200px;text-align:center;color:var(--white);font-size:15px;line-height:20px}

/* projects */
.projects{top:699px;left:0;width:1200px;height:756px;background:linear-gradient(180deg,#f4f7fa 0%,#e6f1f7 60%,#d9ecf5 100%)}
.card{position:absolute;top:315px;height:325px;border:3px solid var(--frame)}
.card__title{position:absolute;top:180px;width:100%;text-align:center;font-weight:600;font-size:18px;color:var(--navy-deep)}
.card__body{position:absolute;top:218px;width:100%;text-align:center;font-size:13px;line-height:16px}

/* about */
.about{top:1455px;left:0;width:1200px;height:644px;background:linear-gradient(180deg,#c9e7f4 0%,#d8eef7 100%)}
.about__text{position:absolute;left:84px;top:253px;width:410px;font-size:15px;line-height:30px}

/* services */
.services{top:2099px;left:0;width:1200px;height:1284px;background:linear-gradient(180deg,#eef5f8 0%,#b9e0f1 30%,#7fcbee 70%,#cfe9f4 100%)}
.svc-num{position:absolute;left:65px;width:66px;height:66px;border-radius:50%;background:var(--navy);color:var(--white);font-weight:700;font-size:32px;display:flex;align-items:center;justify-content:center}
.svc-text{position:absolute;left:143px;font-weight:600;font-size:27px;line-height:37px;color:var(--navy);white-space:nowrap}

/* portfolio */
.portfolio{top:3383px;left:0;width:1200px;height:930px;background:linear-gradient(180deg,#f5f8fa 0%,#d6edf6 50%,#aedcf0 100%)}
.rule{position:absolute;height:3px;background:var(--navy)}
.arrow{position:absolute;width:52px;height:52px;border-radius:50%;display:flex;align-items:center;justify-content:center}

/* testimonials */
.testimonials{top:4313px;left:0;width:1200px;height:542px;background:linear-gradient(180deg,#7ccff0 0%,#5fc0ea 100%)}
.quote{position:absolute;font-size:14px;line-height:18px;font-style:italic;color:var(--white)}
.quote__mark{position:absolute;font-size:44px;font-weight:700;color:var(--white);line-height:1}
.quote__name{position:absolute;font-size:12px;font-weight:600;color:var(--white);white-space:nowrap}
.quote__stars{position:absolute;font-size:22px;letter-spacing:3px;color:var(--white)}

/* footer */
.footer{top:4855px;left:0;width:1200px;height:353px;background:var(--navy)}
.footer h4{position:absolute;top:98px;font-size:13px;font-weight:600;color:var(--white)}
.footer__links{position:absolute;left:456px;top:136px;list-style:none}
.footer__links li{font-size:12px;color:var(--white);height:25.5px}
.footer__links li::before{content:"› ";}
.footer__contact{position:absolute;left:664px;font-size:13px;line-height:16px;color:var(--white)}
.footer__icon{position:absolute;left:621px;width:30px;height:30px;border-radius:50%;background:var(--white);display:flex;align-items:center;justify-content:center}
.field{position:absolute;left:877px;width:243px;height:47px;border-radius:8px;background:#e9edf3;color:#8a93a8;font-size:14px;display:flex;align-items:center;padding-left:24px}
.copyright{top:5208px;left:0;width:1200px;height:60px;background:var(--sky);display:flex;align-items:center;justify-content:center;font-size:12px;color:var(--navy)}
</style>
</head>
<body>
<div class="page">

  <!-- top bar -->
  <div class="abs topbar">
    <span class="social" style="left:62px"></span>
    <span class="social" style="left:98px"></span>
    <span class="social" style="left:134px"></span>
    <span class="social" style="left:170px"></span>
    <div class="topbar__item" style="left:738px">
      <span class="topbar__icon"><svg width="12" height="12" viewBox="0 0 24 24"><path fill="#fff" d="M6.6 10.8a15 15 0 006.6 6.6l2.2-2.2c.3-.3.7-.4 1-.2 1.1.4 2.3.6 3.6.6.6 0 1 .4 1 1V20c0 .6-.4 1-1 1A17 17 0 013 4c0-.6.4-1 1-1h3.5c.6 0 1 .4 1 1 0 1.3.2 2.5.6 3.6.1.3 0 .7-.2 1z"/></svg></span>
      <span>CALL  US TODAY : 123 456 7890</span>
    </div>
    <div class="topbar__item" style="left:957px">
      <span class="topbar__icon"><svg width="12" height="12" viewBox="0 0 24 24"><path fill="#fff" d="M2 5h20v14H2z"/><path fill="none" stroke="#0d1f5c" stroke-width="2" d="M2 5l10 8 10-8"/></svg></span>
      <span>Email : xxxxx@mailbox.com</span>
    </div>
  </div>

  <!-- header -->
  <header class="abs header">
    <div class="brand" style="left:57px;top:24px"><span class="brand__dot"></span><span class="brand__name"><span>CALLOWAY</span><span>AQUATICS</span></span></div>
    <nav class="nav">
      <a style="left:388px">HOME</a>
      <a style="left:454px">ABOUT US</a>
      <a style="left:542px">PROJECTS <span style="color:var(--sky)">▾</span></a>
      <a style="left:636px">PORTFOLIO</a>
      <a style="left:734px">TESTIMONIALS</a>
      <a style="left:854px">CONTACT</a>
    </nav>
    <span class="pill pill--sky" style="left:961px;top:29px;width:167px;height:40px;font-size:13px;font-weight:500">Request a quote</span>
  </header>

  <!-- hero -->
  <section class="abs hero" role="img" aria-label="Photo of a luxury resort pool with lounge chairs at the edge">
    <h1 class="hero__title">DESIGN AND INSTALL HIGH-END<br>COMMERCIAL POOLS</h1>
    <p class="hero__sub">Lorem ipsum dolor sit amet, consectetur adipiscing elit,<br>sed do eiusmod tempor incididunt ut labore et dolore magna aliquaUt enim ad minim</p>
    <span class="pill pill--sky" style="left:484px;top:422px;width:232px;height:49px;font-size:17px">Request a quote</span>
  </section>

  <!-- projects -->
  <section class="abs projects">
    <span class="ghost-word" style="left:1100px;top:140px;color:rgba(230,170,190,.35)">PROJECT</span>
    <h2 class="section-title" style="top:72px">PROJECT WE SPECIALIZE IN</h2>

    <div class="card" style="left:94px;width:317px">
      <div class="card__title">LOREM IPSUM DOLOR</div>
      <p class="card__body">Lorem ipsum dolor sit amet,<br>consectetur adipiscing elit,<br>sed do eiusmod tempor incididunt</p>
      <span class="pill pill--navy" style="left:92px;top:298px;width:131px;height:34px">Read more</span>
    </div>
    <div class="card" style="left:431px;width:309px">
      <div class="card__title">LOREM IPSUM DOLOR</div>
      <p class="card__body">Lorem ipsum dolor sit amet,<br>consectetur adipiscing elit,<br>sed do eiusmod tempor incididunt</p>
      <span class="pill pill--navy" style="left:89px;top:298px;width:131px;height:34px">Read more</span>
    </div>
    <div class="card" style="left:762px;width:317px">
      <div class="card__title">LOREM IPSUM DOLOR</div>
      <p class="card__body">Lorem ipsum dolor sit amet,<br>consectetur adipiscing elit,<br>sed do eiusmod tempor incididunt</p>
      <span class="pill pill--navy" style="left:93px;top:298px;width:131px;height:34px">Read more</span>
    </div>
    <div class="photo" style="left:132px;top:214px;width:246px;height:246px;background:radial-gradient(circle at 40% 45%,#6cc3e4,#2a8fc4 70%,#8c8a80)" role="img" aria-label="Outdoor pool with a metal ladder"></div>
    <div class="photo" style="left:468px;top:214px;width:246px;height:246px;background:linear-gradient(180deg,#b8cbd9 0%,#c9b89a 35%,#e8e6e0 45%,#3e9fd6 60%,#2877c0 100%)" role="img" aria-label="Rectangular pool behind a white fence"></div>
    <div class="photo" style="left:797px;top:214px;width:246px;height:246px;background:radial-gradient(circle at 45% 50%,#3dbfd9,#1a8ab0 55%,#3c5a3a 90%)" role="img" aria-label="Swimmer floating in a lagoon pool among rocks and palms"></div>
  </section>

  <!-- about -->
  <section class="abs about">
    <span class="ghost-word" style="left:1100px;top:140px">ABOUT</span>
    <h2 class="abs" style="left:88px;top:130px;font-size:50px;font-weight:700;color:var(--navy)">ABOUT US</h2>
    <p class="about__text">Lorem ipsum dolor sit amet, consectetur adipiscing elit,&nbsp; sed do eiusmod tempor incididunt ut labore et dolore magna aliqua.&nbsp; Ut enim ad minim veniam, quis nostrud exercitation ullamco laboris nisi uT.....</p>
    <span class="pill pill--navy" style="left:82px;top:468px;width:149px;height:43px;font-size:13px;font-weight:500">Read more</span>
    <div class="photo" style="left:583px;top:94px;width:458px;height:458px;border-width:10px;background:linear-gradient(180deg,#d9cfc2 0%,#cbbfae 38%,#e8eef0 45%,#2f9ad8 60%,#1a6fc0 100%)" role="img" aria-label="Indoor tiled pool with a sauna cabin and lounge area"></div>
  </section>

  <!-- services -->
  <section class="abs services">
    <span class="ghost-word" style="left:1100px;top:360px;color:rgba(255,255,255,.45)">SERVICES</span>
    <h2 class="section-title" style="top:82px">HIGH END NATURE OF SERVICES</h2>

    <span class="svc-num" style="top:274px">1</span>
    <p class="svc-text" style="top:270px">THE 57TH FLOOR SPA AT<br>THE PHILA SILVER WILLOW</p>
    <span class="svc-num" style="top:376px">2</span>
    <p class="svc-text" style="top:374px">THE AQUATIC THERAPY PORTION OF<br>THE PHILA RAVENHAWKS TRAINING FACILITY</p>
    <span class="svc-num" style="top:478px">3</span>
    <p class="svc-text" style="top:475px">A 5OM INDOOR COMPETITION POOL FOR<br>THE PRESTIGIOUS DALLOWMERE ACADEMY</p>
    <span class="svc-num" style="top:589px">4</span>
    <p class="svc-text" style="top:590px">THE INDOOR WATER PARK AT<br>THE QUENWICK LODGE</p>
    <span class="svc-num" style="top:693px">5</span>
    <p class="svc-text" style="top:707px">COUNTRY CLUB RENOVATION PROJECT</p>

    <div class="photo" style="left:756px;top:190px;width:348px;height:348px;background:linear-gradient(180deg,#6b5a45 0%,#9a8a70 40%,#9fc79a 65%,#7fb38a 100%)" role="img" aria-label="Indoor spa plunge pool with stone walls"></div>
    <div class="photo" style="left:756px;top:507px;width:348px;height:348px;background:radial-gradient(circle at 45% 45%,#8fd4f0,#3aa4dc 60%,#1f7fc2)" role="img" aria-label="Swimmer floating on her back in clear blue water"></div>
    <div class="photo" style="left:92px;top:834px;width:348px;height:348px;background:linear-gradient(180deg,#bcd8ea 0%,#5d8c5a 40%,#4fb6d6 70%,#2f96c8 100%)" role="img" aria-label="Resort pool with water slides and palm trees"></div>
    <div class="photo" style="left:419px;top:834px;width:348px;height:348px;background:linear-gradient(180deg,#7a4a3a 0%,#b9a48c 30%,#5cc9df 50%,#2aa7cf 100%)" role="img" aria-label="Dog swimming in an outdoor pool"></div>
    <div class="photo" style="left:760px;top:834px;width:348px;height:348px;background:radial-gradient(circle at 50% 50%,#7fd0f0,#2a9ee0 60%,#1a7cc8)" role="img" aria-label="Swimmer doing freestyle in a lane"></div>
  </section>

  <!-- portfolio -->
  <section class="abs portfolio">
    <span class="ghost-word" style="left:1090px;top:330px;color:rgba(255,255,255,.5)">PORTFOLIO</span>
    <h2 class="section-title" style="top:115px">OUR PORTFOLIO</h2>
    <div class="photo" style="left:122px;top:327px;width:348px;height:348px;background:linear-gradient(180deg,#cfd8df 0%,#5ab0e0 30%,#1f7fcc 100%)" role="img" aria-label="Indoor lap pool with blue tiles"></div>
    <div class="photo" style="left:736px;top:327px;width:348px;height:348px;background:linear-gradient(180deg,#eae5dc 0%,#8a6a52 45%,#52c2d8 65%,#2aa0c4 100%)" role="img" aria-label="Hotel courtyard pool with lounge chairs"></div>
    <div class="photo" style="left:354px;top:266px;width:490px;height:490px;border-width:10px;background:linear-gradient(180deg,#b9a890 0%,#c8b8a0 25%,#5cc8e4 38%,#2aa3d4 62%,#cbb8a0 76%,#a08c74 100%)" role="img" aria-label="Aerial view of a swimmer in a rectangular pool"></div>
    <span class="rule" style="left:123px;top:837px;width:388px"></span>
    <span class="rule" style="left:691px;top:837px;width:388px"></span>
    <span class="arrow" style="left:540px;top:812px;background:var(--navy)"><svg width="18" height="18" viewBox="0 0 24 24"><path d="M15 4l-8 8 8 8" fill="none" stroke="#fff" stroke-width="2.5"/></svg></span>
    <span class="arrow" style="left:608px;top:812px;background:var(--sky)"><svg width="18" height="18" viewBox="0 0 24 24"><path d="M9 4l8 8-8 8" fill="none" stroke="#fff" stroke-width="2.5"/></svg></span>
  </section>

  <!-- testimonials -->
  <section class="abs testimonials">
    <span class="ghost-word" style="left:1100px;top:140px;color:rgba(255,255,255,.3)">TESTIMONI</span>
    <h2 class="section-title" style="top:55px">TESTIMONIALS</h2>

    <div class="photo" style="left:76px;top:203px;width:142px;height:142px;border-width:5px;background:linear-gradient(180deg,#c9d2da,#e8e2dc)" role="img" aria-label="Portrait of a smiling client"></div>
    <span class="quote__mark" style="left:228px;top:202px">“</span>
    <p class="quote" style="left:265px;top:207px;width:250px">Lorem ipsum dolor sit amet, consectetur adipiscing elit, sed do eiusmod tempor incididunt ut labore et dolore magna</p>
    <span class="quote__mark" style="left:488px;top:272px">”</span>
    <span class="quote__name" style="left:265px;top:293px">Miles Corran, Speedline Driver</span>
    <span class="quote__stars" style="left:272px;top:312px">★★★★</span>

    <div class="photo" style="left:640px;top:203px;width:142px;height:142px;border-width:5px;background:linear-gradient(180deg,#b8a898,#d6d2cc)" role="img" aria-label="Portrait of a smiling client"></div>
    <span class="quote__mark" style="left:780px;top:202px">“</span>
    <p class="quote" style="left:807px;top:226px;width:250px">Lorem ipsum dolor sit amet, consectetur adipiscing elit, sed do eiusmod tempor incididunt.</p>
    <span class="quote__mark" style="left:1058px;top:245px">”</span>
    <span class="quote__name" style="left:828px;top:293px">Miles Corran, Speedline Driver</span>
    <span class="quote__stars" style="left:835px;top:312px">★★★★</span>

    <span class="rule" style="left:123px;top:457px;width:388px"></span>
    <span class="rule" style="left:691px;top:457px;width:388px"></span>
    <span class="arrow" style="left:540px;top:432px;background:var(--navy)"><svg width="18" height="18" viewBox="0 0 24 24"><path d="M15 4l-8 8 8 8" fill="none" stroke="#fff" stroke-width="2.5"/></svg></span>
    <span class="arrow" style="left:608px;top:432px;background:var(--white)"><svg width="18" height="18" viewBox="0 0 24 24"><path d="M9 4l8 8-8 8" fill="none" stroke="#3ab4e6" stroke-width="2.5"/></svg></span>
  </section>

  <!-- footer -->
  <footer class="abs footer">
    <div class="brand" style="left:102px;top:100px;color:var(--white)"><span class="brand__dot"></span><span class="brand__name"><span>CALLOWAY</span><span>AQUATICS</span></span></div>

    <h4 style="left:452px">QUICK LINKS</h4>
    <ul class="footer__links">
      <li>HOME</li><li>ABOUT US</li><li>PROJECTS</li><li>PORTFOLIO</li><li>TESTIMONIALS</li><li>CONTACT</li>
    </ul>

    <h4 style="left:621px;top:94px">CONTACT US</h4>
    <span class="footer__icon" style="top:138px"><svg width="14" height="14" viewBox="0 0 24 24"><path fill="#0d1f5c" d="M12 2a7 7 0 00-7 7c0 5 7 13 7 13s7-8 7-13a7 7 0 00-7-7zm0 9.5A2.5 2.5 0 1112 6a2.5 2.5 0 010 5.5z"/></svg></span>
    <p class="footer__contact" style="top:139px">Location Name<br>Dummy address here<br>Pin: 123456</p>
    <span class="footer__icon" style="top:199px"><svg width="14" height="14" viewBox="0 0 24 24"><path fill="#0d1f5c" d="M6.6 10.8a15 15 0 006.6 6.6l2.2-2.2c.3-.3.7-.4 1-.2 1.1.4 2.3.6 3.6.6.6 0 1 .4 1 1V20c0 .6-.4 1-1 1A17 17 0 013 4c0-.6.4-1 1-1h3.5c.6 0 1 .4 1 1 0 1.3.2 2.5.6 3.6.1.3 0 .7-.2 1z"/></svg></span>
    <p class="footer__contact" style="top:200px">123 456 7890<br>258 963 7410</p>
    <span class="footer__icon" style="top:252px"><svg width="14" height="14" viewBox="0 0 24 24"><path fill="#0d1f5c" d="M2 5h20v14H2z"/><path fill="none" stroke="#fff" stroke-width="2" d="M2 5l10 8 10-8"/></svg></span>
    <p class="footer__contact" style="top:259px">Email:&nbsp; xxxxx@mailbox.com</p>

    <h4 style="left:891px">NEWS LETTER</h4>
    <span class="field" style="top:130px">Enter&nbsp; Name</span>
    <span class="field" style="top:189px">Enter Email Address</span>
    <span class="abs" style="left:881px;top:259px;width:106px;height:31px;background:var(--sky);color:var(--white);font-size:13px;font-weight:600;display:flex;align-items:center;justify-content:center">SUBMIT</span>
  </footer>
  <div class="abs copyright">Copyright © 2023 All rights reserved</div>

</div>
</body>
</html>
```